Home Page PSD Website Design - 1 Page *

Design an eye-catching home page design for a rubbish removal website.

Please review the document provided it contains all the details and there is a second document with all the content for the page that needs to be included.

Target Market(s)

Home owners, businesses, property managers, real estate agents

Industry/Entity Type

Waste Management

Number of Pages Required

1 page

Requirements
Must have
• Please review the document provided it contains all the details and there is a second document with all the content for the page that needs to be included.

PSD must be layered, all elements labeled and separated for easy coding.
Nice to have

```html
<!DOCTYPE html>
<html lang="en">
<head>
<meta charset="utf-8">
<title>Swift Haul Junk Removal</title>
<link href="https://fonts.googleapis.com/css2?family=Oswald:wght@400;500;600&family=Roboto:wght@400;500;700&display=swap" rel="stylesheet">
<style>
:root{
  --blue:#0b5fad;
  --blue-deep:#0d4c93;
  --lime:#d6ea00;
  --ink:#1c1c1c;
  --muted:#555;
  --field:#e4e9ef;
  --dark:#171a1d;
  --white:#fff;
}
*{box-sizing:border-box;margin:0;padding:0}
html,body{width:1200px;height:4614px;overflow:hidden}
body{position:relative;background:var(--white);font-family:Roboto,Arial,sans-serif;color:var(--ink)}
.abs{position:absolute}
.head{font-family:Oswald,"Arial Narrow",sans-serif;font-weight:500;letter-spacing:-.2px}
.fill{border-radius:0}

/* header */
.site-header{left:0;top:0;width:1200px;height:74px;background:var(--white)}
.brand{left:200px;top:22px;font-family:Oswald,sans-serif;font-weight:600;font-size:21px;color:var(--blue);display:flex;align-items:center;gap:8px;text-transform:uppercase}
.brand-dot{width:14px;height:14px;background:var(--lime);border-radius:50%}
.nav{left:446px;top:30px;display:flex;gap:0;font-family:Oswald,sans-serif;font-size:12.5px}
.nav a{color:var(--ink);text-decoration:none;margin-right:39px}
.nav-cta{left:890px;top:25px;width:108px;height:33px;background:var(--blue);color:var(--white);font-family:Oswald,sans-serif;font-size:12.5px;display:flex;align-items:center;justify-content:center;clip-path:polygon(6% 0,100% 0,94% 100%,0 100%)}

/* hero */
.hero{left:0;top:74px;width:1200px;height:490px;background:linear-gradient(90deg,#26548e 0%,#3b6aa3 45%,#9aa4ad 75%,#6f7c86 100%)}
.hero-truck{left:570px;top:110px;width:630px;height:380px;background:linear-gradient(180deg,#8ec63f 0%,#6aa42c 60%,#d9dde0 61%,#e9ecee 100%);border-radius:6px}
.estimate-card{left:200px;top:95px;width:371px;height:449px;background:var(--white);border-radius:6px;padding:24px 45px}
.estimate-card h2{font-family:Oswald,sans-serif;font-weight:500;font-size:24px;text-align:center;line-height:1.15;margin-bottom:20px}
.field{height:34px;background:var(--field);margin:0 0 10px 10px;font-family:Oswald,sans-serif;font-size:10.5px;padding:9px 16px;color:#333}
.field.msg{height:84px}
.submit{margin:12px 0 0 10px;height:34px;background:var(--blue-deep);color:var(--white);font-family:Oswald,sans-serif;font-size:12px;display:flex;align-items:center;justify-content:center}

/* intro */
.intro-img{left:200px;top:620px;width:463px;height:358px;background:linear-gradient(135deg,#a9c2d8,#7aa23a 50%,#c9b98a)}
.intro-panel{left:564px;top:655px;width:435px;height:267px;background:var(--blue);color:var(--white);padding:25px 30px 0 94px;clip-path:polygon(14% 0,100% 0,100% 100%,0 100%)}
.intro-stripe{left:650px;top:620px;width:14px;height:358px;background:var(--lime);transform:skewX(-20deg);transform-origin:top}
.intro-panel h2{font-size:25px;margin-bottom:10px}
.intro-panel p{font-size:10.5px;line-height:1.95}
.phone{margin-top:10px;display:flex;gap:10px;align-items:center;font-family:Oswald,sans-serif;font-size:17px;color:var(--lime)}

/* what we do */
.section-title{width:1200px;left:0;text-align:center;font-size:24px}
.lede{left:390px;width:420px;text-align:center;font-size:10px;line-height:1.4;color:#333}
.service{top:1175px;width:188px;height:367px;background:var(--white);box-shadow:0 4px 14px rgba(0,0,0,.12)}
.service .pic{height:162px;background:linear-gradient(160deg,#b9c8d6,#8c8c82)}
.service .bar{height:5px;background:var(--lime);transform:skewY(-2.5deg);margin-top:-3px}
.service h3{font-family:Oswald,sans-serif;font-weight:500;font-size:18px;line-height:1.25;padding:20px 20px 8px}
.service .rule{width:30px;height:3px;background:var(--blue);margin:6px 20px 14px}
.service p{font-size:9.5px;line-height:1.3;color:#666;padding:0 20px}

/* quote band */
.quote-photo{left:520px;top:1599px;width:680px;height:357px;background:linear-gradient(120deg,#c4b38c,#d6cf4a 45%,#a7b4bd)}
.quote-band{left:0;top:1623px;width:640px;height:310px;background:var(--blue);clip-path:polygon(0 0,100% 0,81% 100%,0 100%);color:var(--white);padding:38px 0 0 201px}
.quote-stripe{left:515px;top:1623px;width:10px;height:310px;background:var(--lime);transform:skewX(-31deg);transform-origin:top}
.quote-band h2{font-size:24px;margin-bottom:14px}
.quote-band p{font-size:10.5px;line-height:2;width:330px}
.ghost-btn{display:inline-flex;margin-top:22px;background:var(--white);color:var(--ink);font-family:Oswald,sans-serif;font-size:12px;height:29px;padding:0 28px;align-items:center;clip-path:polygon(5% 0,100% 0,95% 100%,0 100%)}

/* before after */
.ba{top:2088px;width:184px;height:249px;background:linear-gradient(180deg,#a3876a,#6b5a48)}
.ba-tag{position:absolute;left:30px;top:188px;width:110px;height:24px;background:#111;color:var(--lime);font-family:Oswald,sans-serif;font-size:12px;letter-spacing:3px;display:flex;align-items:center;justify-content:center;clip-path:polygon(6% 0,100% 0,94% 100%,0 100%)}
.ba-split{left:600px;top:2090px;width:3px;height:245px;background:var(--lime);transform:skewX(-5deg)}
.pill-btn{width:109px;height:29px;background:var(--blue);color:var(--white);font-family:Oswald,sans-serif;font-size:12px;display:flex;align-items:center;justify-content:center;clip-path:polygon(6% 0,100% 0,94% 100%,0 100%)}

/* specialty tiles */
.tile{width:131px;height:132px;background:var(--blue);color:var(--white);display:flex;flex-direction:column;align-items:center;justify-content:center;gap:10px;font-size:14px;text-align:center;line-height:1.25;box-shadow:-6px 6px 0 rgba(10,60,120,.35)}
.tile svg{width:26px;height:26px}

/* steps */
.supplies{left:85px;top:2991px;width:1030px;height:197px;background:linear-gradient(90deg,#e33a2d 0%,#1f6fd8 16%,#2f7ac8 33%,#2f7a6a 52%,#f2c900 75%,#2b4f9a 100%);border-radius:40px 40px 0 0}
.steps-band{left:0;top:3188px;width:1200px;height:333px;background:var(--blue)}
.steps-line{left:0;top:3519px;width:1200px;height:5px;background:var(--lime)}
.steps-title{left:0;top:3258px;width:1200px;text-align:center;color:var(--white);font-size:24px;line-height:1.3}
.step{top:3374px;width:261px;height:287px;background:var(--white);box-shadow:0 4px 14px rgba(0,0,0,.15);text-align:center;padding-top:32px}
.step .badge{width:60px;height:60px;border-radius:50%;background:var(--lime);margin:0 auto 24px;display:flex;align-items:center;justify-content:center}
.step h3{font-family:Oswald,sans-serif;font-weight:500;font-size:22px;margin-bottom:20px}
.step p{font-size:11px;line-height:1.35;color:#444;padding:0 44px}

/* testimonial */
.testi-photo{left:200px;top:3725px;width:463px;height:358px;background:linear-gradient(135deg,#3f4a3f,#262b28 60%,#3a4336)}
.testi-stripe{left:560px;top:3725px;width:10px;height:358px;background:var(--lime);transform:skewX(-18deg);transform-origin:top}
.testi-copy{left:258px;top:3810px;width:280px;color:var(--white)}
.testi-copy h2{font-size:24px;margin-bottom:12px}
.testi-copy p{font-size:11px;line-height:1.3}
.testi-panel{left:564px;top:3761px;width:435px;height:260px;background:var(--blue);clip-path:polygon(12% 0,100% 0,100% 100%,0 100%);color:var(--white)}
.avatar{left:655px;top:3810px;width:38px;height:38px;border-radius:50%;background:linear-gradient(180deg,#e9e9e9,#9fb5cc);border:2px solid var(--white)}
.dots{display:flex;gap:5px}
.dots i{width:5px;height:5px;border-radius:50%;background:#7fa6d2}
.dots i:first-child{background:var(--lime)}

/* cta */
.cta-band{left:0;top:4137px;width:1200px;height:254px;background:var(--blue);color:var(--white)}
.cta-band h2{position:absolute;left:200px;top:44px;font-size:24px}
.cta-band p{position:absolute;left:200px;top:100px;width:530px;font-size:11px;line-height:1.35}
.cta-art{left:775px;top:4095px;width:200px;height:300px;background:linear-gradient(180deg,#c27a3f,#2b6ed0 55%,#e0c23a);border-radius:40% 40% 10% 10%}

/* footer */
.site-footer{left:0;top:4391px;width:1200px;height:223px;background:var(--dark);color:#cfcfcf}
.fcol{position:absolute;top:60px;font-size:9.5px;line-height:1.4}
.fcol h4{font-family:Oswald,sans-serif;font-weight:500;font-size:10.5px;color:var(--white);margin-bottom:14px}
.finput{height:26px;border:1px solid #666;font-size:9px;color:#ddd;display:flex;align-items:center;padding:0 14px;margin-top:16px}
.social{display:flex;gap:22px;margin-top:18px}
.social i{width:10px;height:10px;border-radius:50%;background:#9aa3ad}
.copyright{left:200px;top:196px;font-size:8px;color:#888}
.privacy{left:940px;top:196px;font-size:8px;color:#888}
.side-tab{left:1170px;width:30px;height:30px;background:var(--blue);display:flex;align-items:center;justify-content:center}
</style>
</head>
<body>

<header class="abs site-header">
  <div class="abs brand"><span class="brand-dot"></span>Swift Haul</div>
  <nav class="abs nav"><a>Home</a><a>Available Services</a><a>Easy Online Quotes</a><a>Service Areas</a><a>FAQ</a></nav>
  <div class="abs nav-cta">Contact Us</div>
</header>

<section class="abs hero" role="img" aria-label="Blue-tinted photo of a garage cluttered with junk"></section>
<div class="abs hero-truck" role="img" aria-label="Illustration of a green and white junk removal truck"></div>
<form class="abs estimate-card">
  <h2>REQUEST A FREE<br>ESTIMATE</h2>
  <div class="field">First Name</div>
  <div class="field">Last Name</div>
  <div class="field">Phone Number</div>
  <div class="field">Email Id</div>
  <div class="field msg">Message</div>
  <div class="submit">Submit Now</div>
</form>

<div class="abs intro-img" role="img" aria-label="Cartoon superhero carrying a trash can in front of a junk pile"></div>
<div class="abs intro-panel">
  <h2 class="head">Got Junk To Haul? Give Us A Call!</h2>
  <p>Has your Lakeview home, garage, basement, yard or place of business become cluttered with old appliances, furniture, electronics, yard debris, garbage or unwanted items that you have no use for? Call Swift Haul Junk Removal today and let us help make extra space in your home and around your property</p>
  <div class="phone"><svg width="16" height="16" viewBox="0 0 24 24"><path fill="#d6ea00" d="M6.6 10.8a15 15 0 0 0 6.6 6.6l2.2-2.2a1 1 0 0 1 1-.25 11.4 11.4 0 0 0 3.6.57 1 1 0 0 1 1 1V20a1 1 0 0 1-1 1A17 17 0 0 1 3 4a1 1 0 0 1 1-1h3.5a1 1 0 0 1 1 1c0 1.25.2 2.45.57 3.6a1 1 0 0 1-.25 1z"/></svg>(555) 302-7781</div>
</div>
<div class="abs intro-stripe"></div>

<h2 class="abs section-title head" style="top:1026px">What We Do</h2>
<p class="abs lede" style="top:1077px">Whether you’re a Lakeview homeowner, real estate agent, business owner, contractor, landlord, property manager or handling an estate, we’ve got you covered with our hassle-free &amp; swift junk removal services</p>

<article class="abs service" style="left:193px"><div class="pic" role="img" aria-label="Photo of a suburban house"></div><div class="bar"></div><h3>Residential<br>Services</h3><div class="rule"></div><p>We know how quickly unwanted items, junk &amp; debris can pile up inside and outside of your home. With our fast, reliable junk removal service</p></article>
<article class="abs service" style="left:397px"><div class="pic" role="img" aria-label="Photo of a commercial office building"></div><div class="bar"></div><h3>Commercial<br>Services</h3><div class="rule"></div><p>Our commercial junk removal service includes the cleanup of offices, retail spaces, warehouses, storage units and any other commercial space .</p></article>
<article class="abs service" style="left:601px"><div class="pic" role="img" aria-label="Photo of an apartment tower"></div><div class="bar"></div><h3>Property<br>Managers</h3><div class="rule"></div><p>We help property managers clear out clutter as well as take old furniture, appliances, trash and mattresses that tenants left behind or have dumped illegally on the property</p></article>
<article class="abs service" style="left:805px"><div class="pic" role="img" aria-label="Photo of an excavator on a demolition site"></div><div class="bar"></div><h3>Construction<br>Debris</h3><div class="rule"></div><p>Keeping the lights on for your business is of major importance. As a family run business ourselves, we value the trust you place in us when you enlist us for your commercial electrical needs.</p></article>

<div class="abs quote-photo" role="img" aria-label="Photo of a worker in a hard hat and safety vest in front of a recycling pile"></div>
<section class="abs quote-band">
  <h2 class="head">Get Your Easy Online Quote Today!</h2>
  <p>We make it really easy for you to receive your junk removal quote. With the power of the internet there is no need to disrupt your busy schedule with an in-person quote. To get started simply click the link below and you will be taken to our online quote form. You will receive your junk removal quote quickly and hassle free.</p>
  <span class="ghost-btn">Click Here</span>
</section>
<div class="abs quote-stripe"></div>

<h2 class="abs section-title head" style="top:2008px">Before And After</h2>
<div class="abs ba" style="left:200px" role="img" aria-label="Garage full of junk before cleanup"><span class="ba-tag">BEFORE</span></div>
<div class="abs ba" style="left:391px" role="img" aria-label="Empty garage after cleanup"><span class="ba-tag">AFTER</span></div>
<div class="abs ba-split"></div>
<div class="abs ba" style="left:625px" role="img" aria-label="Room piled with boxes before cleanup"><span class="ba-tag">BEFORE</span></div>
<div class="abs ba" style="left:815px" role="img" aria-label="Empty room after cleanup"><span class="ba-tag">AFTER</span></div>
<div class="abs pill-btn" style="left:546px;top:2382px">View More</div>

<h2 class="abs section-title head" style="top:2459px">Junk Removal is Our Specialty</h2>
<p class="abs lede" style="top:2513px;left:340px;width:520px">Over time, every business and household is sure to accumulate a number of unwanted items that end up collecting dust and taking up space. By contacting a junk hauling specialist to help you get rid of those items, you are saving yourself hours of hard work and possibly several trips to the dump. Swift Haul Junk Removal can do all that for you promptly and efficiently, making sure that you don’t have to lift a finger or waste any precious time.</p>

<div class="abs tile" style="left:200px;top:2611px"><svg viewBox="0 0 24 24"><rect x="5" y="4" width="10" height="16" rx="2" fill="#d6ea00" transform="rotate(30 12 12)"/></svg>Carpet</div>
<div class="abs tile" style="left:334px;top:2611px"><svg viewBox="0 0 24 24"><circle cx="12" cy="12" r="8" fill="none" stroke="#d6ea00" stroke-width="3"/></svg>Washers &amp;<br>Dryers</div>
<div class="abs tile" style="left:468px;top:2611px"><svg viewBox="0 0 24 24"><circle cx="12" cy="12" r="9" fill="#d6ea00"/><path d="M12 3v18M3 12h18" stroke="#0b5fad" stroke-width="1.5"/></svg>Play<br>Equipment</div>
<div class="abs tile" style="left:602px;top:2611px"><svg viewBox="0 0 24 24"><path d="M12 3l4 6h-8zM4 19l3-7 4 5zM20 19l-3-7-4 5z" fill="#d6ea00"/></svg>Recyclable<br>Item</div>
<div class="abs tile" style="left:736px;top:2611px"><svg viewBox="0 0 24 24"><rect x="3" y="9" width="18" height="8" rx="2" fill="#d6ea00"/><rect x="6" y="6" width="12" height="5" fill="#d6ea00"/></svg>Furniture</div>
<div class="abs tile" style="left:868px;top:2611px"><svg viewBox="0 0 24 24"><rect x="7" y="3" width="10" height="18" rx="1" fill="#d6ea00"/><path d="M7 9h10" stroke="#0b5fad" stroke-width="1.5"/></svg>Refrigetors</div>
<div class="abs tile" style="left:261px;top:2753px"><svg viewBox="0 0 24 24"><path d="M6 7h12l-1 14H7zM5 5h14v2H5z" fill="#d6ea00"/></svg>Rubbish</div>
<div class="abs tile" style="left:395px;top:2753px"><svg viewBox="0 0 24 24"><path d="M3 11h18v4a4 4 0 0 1-4 4H7a4 4 0 0 1-4-4z" fill="#d6ea00"/></svg>Hot Tubs</div>
<div class="abs tile" style="left:529px;top:2753px"><svg viewBox="0 0 24 24"><rect x="5" y="4" width="14" height="16" fill="none" stroke="#d6ea00" stroke-width="2"/><path d="M9 4v16M14 4v16" stroke="#d6ea00" stroke-width="1.5"/></svg>Mattresses</div>
<div class="abs tile" style="left:661px;top:2753px"><svg viewBox="0 0 24 24"><path d="M8 3l4 2 4-2 5 4-3 3-1-1v12H7V9l-1 1-3-3z" fill="#d6ea00"/></svg>Old Clothing</div>
<div class="abs tile" style="left:793px;top:2753px"><svg viewBox="0 0 24 24"><rect x="3" y="6" width="18" height="4" fill="#d6ea00"/><path d="M5 10v10M19 10v10" stroke="#d6ea00" stroke-width="2"/></svg>Tables</div>
<div class="abs pill-btn" style="left:521px;top:2914px">View More</div>

<div class="abs supplies" role="img" aria-label="Row of bins, buckets, a cleaning caddy, a hard hat and a vacuum cleaner"></div>
<section class="abs steps-band"></section>
<div class="abs steps-line"></div>
<h2 class="abs steps-title head">Getting Rid of Unwanted Items, Junk &amp; Debris is<br>As Easy as 1, 2, 3 !</h2>
<article class="abs step" style="left:200px"><div class="badge"><svg width="26" height="26" viewBox="0 0 24 24"><rect x="4" y="5" width="16" height="11" fill="none" stroke="#222" stroke-width="2"/><path d="M2 19h20" stroke="#222" stroke-width="2"/></svg></div><h3>Step 1</h3><p>Use our easy online quote form to get your quote today!</p></article>
<article class="abs step" style="left:469px"><div class="badge"><svg width="26" height="26" viewBox="0 0 24 24"><rect x="4" y="5" width="16" height="15" fill="none" stroke="#222" stroke-width="2"/><path d="M4 9h16M8 3v4M16 3v4" stroke="#222" stroke-width="2"/></svg></div><h3>Step 2</h3><p>Schedule a day that works best for you. Same day, next day and after hour appointments are available</p></article>
<article class="abs step" style="left:738px"><div class="badge"><svg width="26" height="26" viewBox="0 0 24 24"><circle cx="12" cy="8" r="4" fill="none" stroke="#222" stroke-width="2"/><path d="M4 21c1-5 4-7 8-7s7 2 8 7" fill="none" stroke="#222" stroke-width="2"/></svg></div><h3>Step 3</h3><p>When our friendly, uniformed team arrives they make everything super simple for you! All you have to do is point to your unwanted items and we’ll make them disappear</p></article>

<div class="abs testi-photo" role="img" aria-label="Dark photo of a worker loading trash bags"></div>
<div class="abs testi-copy">
  <h2 class="head">Our Testimonial</h2>
  <p>Lorem ipsum dolor sit amet, consectetur adipiscing elit, sed do eiusmod tempor incididunt ut labore et dolore magna aliqua. Quis ipsum suspendisse ultrices gravida. Risus commodo viverra maecenas accumsan lacus vel facilisis.</p>
  <div class="pill-btn" style="margin-top:36px;width:111px;height:26px">View More</div>
</div>
<div class="abs testi-stripe"></div>
<section class="abs testi-panel">
  <svg class="abs" style="left:330px;top:4px" width="80" height="62" viewBox="0 0 80 62"><path d="M0 0h32v30L14 62H2l10-30H0zM44 0h32v30L58 62H46l10-30H44z" fill="#fff" opacity=".35"/></svg>
  <div class="abs head" style="left:160px;top:56px;font-size:13px">DANIEL REYES</div>
  <div class="abs" style="left:160px;top:76px;font-size:8px">Lorem Ipsum</div>
  <p class="abs" style="left:96px;top:108px;width:320px;font-size:8.5px;line-height:1.55">It is a long established fact that a reader will be distracted by the readable content of a page when looking at its layout. The point of using Lorem Ipsum is that it has a more-or-less normal distribution of letters, as opposed to using 'Content here, content here', making it look like readable English.</p>
  <div class="abs dots" style="left:98px;top:196px"><i></i><i></i><i></i><i></i></div>
</section>
<div class="abs avatar" role="img" aria-label="Customer portrait"></div>

<section class="abs cta-band">
  <h2 class="head">Get Your Easy Online Quote Today!</h2>
  <p>We make it really easy for you to receive your junk removal quote. With the power of the internet there is no need to disrupt your busy schedule with an in-person quote. To get started simply click the link below and you will be taken to our online quote form. You will receive your junk removal quote quickly and hassle free</p>
  <span class="ghost-btn" style="position:absolute;left:200px;top:180px;margin:0">Quote From Click Now</span>
</section>
<div class="abs cta-art" role="img" aria-label="Cartoon superhero lifting a stack of old household items"></div>

<footer class="abs site-footer">
  <div class="abs brand" style="top:50px;left:200px;font-size:20px"><span class="brand-dot"></span>Swift Haul</div>
  <p class="abs" style="left:200px;top:108px;width:160px;font-size:9.5px;line-height:1.3;color:#cfcfcf">Lorem ipsum dolor sit amet, consectetur adipiscing elit, sed do eiusmo</p>
  <div class="fcol" style="left:460px"><h4>CONNECT PEOPLE</h4><p>Connect with us and stay<br>in the loop.</p><div class="social"><i></i><i></i><i></i><i></i></div></div>
  <div class="fcol" style="left:670px"><h4>EMAIL UPDATES</h4><p>Be the first to hear about our<br>Event announcements.</p><div class="finput" style="width:170px">Enter your email id<svg style="margin-left:auto" width="12" height="12" viewBox="0 0 24 24"><path d="M2 12L22 3l-6 18-4-7z" fill="#d6ea00"/></svg></div></div>
  <div class="fcol" style="left:906px"><h4>CONTACT US</h4><p>Question? We've got<br>answer. Try us.</p><div class="finput" style="width:92px;justify-content:center">Email us</div></div>
  <div class="abs copyright">© 2019, ALL RIGHTS RESERVED.</div>
  <div class="abs privacy">Privacy Policy</div>
</footer>
<div class="abs side-tab" style="top:4464px"><svg width="14" height="14" viewBox="0 0 24 24"><path d="M3 4h18v12H8l-5 4z" fill="#fff"/></svg></div>
<div class="abs side-tab" style="top:4496px"><svg width="14" height="14" viewBox="0 0 24 24"><rect x="3" y="6" width="18" height="12" fill="#fff"/></svg></div>

</body>
</html>
```